Tavenhurst Falcons FC Website

We are looking to develop a new website for Tavenhurst FC. Tavenhurst FC has now joined with Tavenhurst Falcons FC and we are looking at a website that can work for both clubs. Tavenhurst FC play in a local park football competition while tavenhurst Falcons are a Semi Professional team that plays in the Ostral Premier Series Competition. What we are after is two separate website off the one platform. I have attached both team logos for you to visualise. Also you can look at the existing tavenhurst website www.tavenhurstfc.net.au. We are looking for a huge improvement in the website and it will be imperative we have links to sponsors and the sponsors can get regular visuals. Weare looking to move this club forward and have a very professional website that can communicate clearly with the community.

Hi All,

Please remember that the website is to represent two clubs;
1. Tavenhurst Falcons FC (Competes in Semi Professional League)
2. Tavenhurst FC (Compete in KPWLT League which is a lower level)

Further to this the Tavenhurst Falcons FC page will require a player profile page which will show photos of each player and a little bio on each.

Thanks

Reason: Would like to spend more time review existing and new designs

```html
<!DOCTYPE html>
<html lang="en">
<head>
<meta charset="utf-8">
<title>Tavenhurst FC</title>
<link href="https://fonts.googleapis.com/css2?family=Exo+2:wght@400;500;600&family=Open+Sans:wght@400;600&display=swap" rel="stylesheet">
<style>
:root{
  --red:#c8141c;
  --red-dark:#9e0f14;
  --ink:#2a2a2a;
  --grey:#6e6e6e;
  --light:#efefef;
  --footer:#1c1c1c;
  --white:#ffffff;
}
*{margin:0;padding:0;box-sizing:border-box}
html,body{width:743px;height:1200px;overflow:hidden;background:var(--white)}
body{position:relative;font-family:"Open Sans",Arial,sans-serif;color:var(--ink)}
.abs{position:absolute}
.heading{font-family:"Exo 2",Arial,sans-serif;font-weight:500;text-transform:uppercase}

/* top + nav */
.top-strip{left:0;top:0;width:743px;height:22px;background:linear-gradient(90deg,#221d18,#5e5040 50%,#221d18)}
.nav{left:0;top:22px;width:743px;height:35px;background:var(--white);border-bottom:1px solid #ddd;z-index:3}
.nav a{position:absolute;top:13px;font-family:"Exo 2",sans-serif;font-size:8px;color:var(--ink);text-decoration:none;text-transform:uppercase;letter-spacing:.2px}
.nav a.active{color:var(--red)}
.nav .active-bar{position:absolute;left:100px;top:33px;width:42px;height:2px;background:var(--red)}
.brand-tab{left:334px;top:2px;width:76px;height:78px;border-radius:50%;background:var(--white);display:flex;align-items:center;justify-content:center;text-align:center;font-family:"Exo 2",sans-serif;font-weight:600;font-size:9px;line-height:11px;color:var(--red);z-index:4;box-shadow:0 2px 4px rgba(0,0,0,.25)}

/* hero */
.hero{left:0;top:57px;width:743px;height:287px;
  background:
    radial-gradient(ellipse 60% 55% at 52% 30%,rgba(236,214,178,.85) 0%,rgba(200,168,124,.5) 45%,rgba(0,0,0,0) 75%),
    radial-gradient(ellipse 70% 35% at 50% 100%,rgba(88,96,52,.9) 0%,rgba(88,96,52,0) 100%),
    linear-gradient(90deg,rgba(30,24,20,.85) 0%,rgba(30,24,20,0) 22%,rgba(30,24,20,0) 78%,rgba(30,24,20,.8) 100%),
    linear-gradient(#b39470 0%,#9a7a55 45%,#6b5a3c 75%,#4a4630 100%)}
.hero-arrow{width:26px;height:26px;border-radius:50%;border:1.5px solid var(--white);display:flex;align-items:center;justify-content:center}
.hero-arrow.next{border-color:var(--red)}
.hero-mark{left:100px;top:154px;width:68px;height:68px;border-radius:50%;background:var(--red)}
.hero-title{left:181px;top:157px;font-size:31px;color:var(--red);letter-spacing:.5px}
.hero-sub{left:182px;top:193px;font-size:8px;color:var(--white)}

/* welcome */
.welcome{left:0;top:344px;width:743px;height:170px;background:#f3f3f3}
.welcome-title{left:100px;top:373px;font-size:27px;line-height:27px;color:var(--ink)}
.welcome-title span{color:var(--red)}
.register{left:100px;top:436px;width:171px;height:46px;background:linear-gradient(#d3161f,var(--red-dark));color:var(--white);padding:9px 0 0 46px;font-family:"Exo 2",sans-serif}
.register small{display:block;font-size:10px}
.register b{font-weight:500;font-size:14px;text-transform:uppercase}
.about-title{left:304px;top:380px;font-size:16px;color:var(--ink)}
.about-title span{color:var(--red)}
.rule{height:1px;background:#444}
.body-text{font-size:8px;line-height:12.8px;color:var(--grey)}

/* fixtures */
.fixtures{left:0;top:514px;width:743px;height:326px;background:#ebebeb}
.fix-title{left:98px;top:547px;font-size:20px;color:var(--red)}
.fix-title span{color:var(--ink)}
.fix-list{list-style:none;font-family:"Exo 2",sans-serif;font-size:9px;text-transform:uppercase;color:#444}
.fix-list li{height:16px;position:relative;padding-left:12px}
.fix-list li::before{content:"";position:absolute;left:0;top:3px;width:5px;height:5px;border:1px solid #444}
.fix-list li.current{color:var(--red)}
.fix-list li.current::before{border-color:var(--red)}
.player{left:505px;top:532px;width:140px;height:308px;
  background:
    radial-gradient(ellipse 30% 48% at 55% 42%,rgba(178,34,46,.75) 0%,rgba(178,34,46,.35) 55%,rgba(235,235,235,0) 100%),
    radial-gradient(ellipse 30% 14% at 30% 88%,rgba(220,220,220,.8) 0%,rgba(235,235,235,0) 100%)}

/* campaign */
.campaign{left:0;top:840px;width:743px;height:144px;background:linear-gradient(90deg,#4e4e4e,#767676 45%,#5a5a5a 70%,#2e2e2e)}
.camp-title{left:238px;top:862px;font-size:18px;color:var(--white)}
.camp-text{color:#e4e4e4}
.btn{left:241px;top:938px;width:71px;height:19px;background:var(--red);color:var(--white);font-family:"Exo 2",sans-serif;font-size:8px;display:flex;align-items:center;justify-content:center}

/* footer */
.footer{left:0;top:984px;width:743px;height:216px;background:var(--footer)}
.foot-title{top:1015px;font-size:11px;color:#aaa}
.foot-rule{top:1038px;height:1px;background:#3a3a3a}
.sitemap{left:100px;top:1047px;list-style:none;font-size:7px;color:#b5b5b5}
.sitemap li{height:16px;padding-left:12px;position:relative}
.sitemap li::before{content:"";position:absolute;left:0;top:3px;width:4px;height:4px;border:1px solid #888}
.news-item{left:263px;width:170px;height:30px}
.news-thumb{position:absolute;left:0;top:0;width:37px;height:26px;background:linear-gradient(#8a8a8a,#4a4a4a)}
.news-item p{position:absolute;left:42px;top:0;font-size:6.5px;line-height:7.5px;color:#ddd;width:120px}
.news-item i{display:block;color:#777;font-size:5.5px;margin-top:1px}
.dot{width:8px;height:8px;border-radius:50%}
.gallery{left:482px;top:1049px;width:160px;height:101px;display:grid;grid-template-columns:1fr 1fr;gap:2px}
.gallery div{background:linear-gradient(#7a6e6a,#3c3a48)}
.copyright{left:100px;top:1176px;font-size:7.5px;color:#888}
.social{top:1174px;width:16px;height:16px;border-radius:50%;border:1px solid #666}
</style>
</head>
<body>

<div class="abs top-strip"></div>
<nav class="abs nav">
  <a class="active" style="left:110px">Home</a>
  <a style="left:150px">About Us</a>
  <a style="left:203px">News</a>
  <a style="left:242px">Fixture &amp; Results</a>
  <a style="left:425px">Photo Gallery</a>
  <a style="left:501px">Sponsor</a>
  <a style="left:552px">Club</a>
  <a style="left:587px">Contact Us</a>
  <span class="active-bar"></span>
</nav>
<div class="abs brand-tab">TAVENHURST<br>FC</div>

<section class="abs hero" role="img" aria-label="Youth footballers striking a ball in a stadium"></section>
<div class="abs hero-arrow" style="left:41px;top:175px"><svg width="8" height="8" viewBox="0 0 8 8"><path d="M5.5 1 2.5 4 5.5 7" fill="none" stroke="#fff" stroke-width="1.3"/></svg></div>
<div class="abs hero-arrow next" style="left:675px;top:175px"><svg width="8" height="8" viewBox="0 0 8 8"><path d="M2.5 1 5.5 4 2.5 7" fill="none" stroke="#c8141c" stroke-width="1.3"/></svg></div>
<div class="abs hero-mark"></div>
<h1 class="abs heading hero-title">Tavenhurst FC</h1>
<p class="abs hero-sub">Lorem Ipsum is simply dummy text typesetting industry.</p>

<section class="abs welcome"></section>
<h2 class="abs heading welcome-title">Welcome to<br><span>Tavenhurst FC</span></h2>
<div class="abs register"><small>2014 Season</small><b>Register Online</b></div>
<h3 class="abs heading about-title">Let’s talk <span>about</span> Tavenhurst FC.</h3>
<div class="abs rule" style="left:304px;top:406px;width:339px"></div>
<p class="abs body-text" style="left:305px;top:417px;width:340px">Lorem Ipsum is simply dummy text of the printing and typesetting industry. Lorem Ipsum has been the industry's standard dummy text ever since the 1500s, when an unknown printer took a galley of type and scrambled it to make a type specimen book. It has survived not only five centuries, but also the leap into electronic typesetting, remaining essentially unchanged.</p>

<section class="abs fixtures"></section>
<h2 class="abs heading fix-title">Fixtures <span>&amp;</span> Results</h2>
<div class="abs rule" style="left:98px;top:581px;width:389px"></div>
<p class="abs body-text" style="left:100px;top:592px;width:385px">Lorem Ipsum is simply dummy text of the printing and typesetting industry. Lorem Ipsum has been the industry's standard dummy text ever since the 1500s, when an unknown printer took a galley of type and scrambled it to make a type specimen book.</p>
<ul class="abs fix-list" style="left:100px;top:652px">
  <li>Premier League</li><li class="current">Premier League Res</li><li>Super League</li><li>Super League Res</li><li>Under 16 / 2</li><li>Under 17 / 1</li><li>Under 10 / 2</li><li>Under 10 / 3</li><li>Under 11 / 1</li><li>Under 12 / 3</li>
</ul>
<ul class="abs fix-list" style="left:263px;top:652px">
  <li>Under 13 / 3</li><li>Under 14 / 3</li><li>AA Men / 5</li><li>AA Men / 6</li><li>AA Men / 8</li><li>AA Men / 10</li><li>AA Men / 10</li><li>AA Men / 14</li><li>07 ECL / Red</li><li>07 ECL / Green</li>
</ul>
<ul class="abs fix-list" style="left:399px;top:652px">
  <li>07 ECL / Blue</li><li>08 ECL / Blue</li><li>08 ECL / Green</li><li>09 / Green</li><li>06 / A Green</li><li>06 / B Blue</li><li>06 / C Red</li><li>06 / D Purple</li><li>06 / E White</li><li>06 / F Brown</li>
</ul>
<div class="abs player" role="img" aria-label="Player in red kit standing with arms crossed beside a ball"></div>

<section class="abs campaign" role="img" aria-label="Blurred stadium backdrop"></section>
<svg class="abs" style="left:100px;top:867px" width="90" height="90" viewBox="0 0 90 90">
  <circle cx="45" cy="45" r="41" fill="#fff"/>
  <circle cx="45" cy="45" r="32" fill="none" stroke="#222" stroke-width="6"/>
  <rect x="20" y="42" width="42" height="9" fill="#222"/>
  <rect x="64" y="42" width="5" height="9" fill="#222"/>
  <line x1="22" y1="22" x2="68" y2="68" stroke="#222" stroke-width="6"/>
</svg>
<h2 class="abs heading camp-title">No Smoking</h2>
<div class="abs rule" style="left:240px;top:895px;width:403px;background:#bbb"></div>
<p class="abs body-text camp-text" style="left:240px;top:904px;width:405px">Lorem Ipsum is simply dummy text of the printing and typesetting industry. Lorem Ipsum has been the industry's standard dummy text ever since the 1500s.</p>
<div class="abs btn">Learn More</div>

<footer class="abs footer"></footer>
<h4 class="abs heading foot-title" style="left:100px">Site Map</h4>
<div class="abs foot-rule" style="left:100px;width:98px"></div>
<ul class="abs sitemap">
  <li>Become A Referee</li><li>News</li><li>Fixture &amp; Results</li><li>Photo Gallery</li><li>Sponsor</li><li>Club</li><li>Contact Us</li>
</ul>
<h4 class="abs heading foot-title" style="left:262px">Latest News</h4>
<div class="abs dot" style="left:402px;top:1018px;background:#555"></div>
<div class="abs dot" style="left:415px;top:1018px;background:var(--red)"></div>
<div class="abs foot-rule" style="left:262px;width:162px"></div>
<div class="abs news-item" style="top:1050px"><div class="news-thumb"></div><p>Lorem Ipsum is simply dummy text of the typesetting industry.<i>Mar 11, 2014</i></p></div>
<div class="abs news-item" style="top:1086px"><div class="news-thumb"></div><p>Lorem Ipsum is simply dummy text of the typesetting industry.<i>Mar 11, 2014</i></p></div>
<div class="abs news-item" style="top:1122px"><div class="news-thumb"></div><p>Lorem Ipsum is simply dummy text of the typesetting industry.<i>Mar 11, 2014</i></p></div>
<h4 class="abs heading foot-title" style="left:482px">Photo Gallery</h4>
<span class="abs" style="left:618px;top:1018px;font-size:6.5px;color:var(--red)">View All</span>
<div class="abs gallery" role="img" aria-label="Grid of club team photos"><div></div><div></div><div></div><div></div></div>
<div class="abs foot-rule" style="left:100px;top:1166px;width:543px"></div>
<p class="abs copyright">Copyright .TAVENHURST FC ® 2014. All rights reserved. Terms and Conditions</p>
<div class="abs social" style="left:550px;border-color:#3d8fd6"></div>
<div class="abs social" style="left:569px"></div>
<div class="abs social" style="left:588px"></div>
<div class="abs social" style="left:607px"></div>
<div class="abs social" style="left:626px"></div>

</body>
</html>
```